Verodex business card

Business card for sustainable investment company called "Verodex". Verodex is an exchange platform selling carbon credits between buyers and sellers. Carbon Credits are an environmental commodity for reducing global carbon emissions.

the card should obviously have our logo and the theme should be sustainability/environment mixed with a trading platform.

Contact Information for Business Card

Logo, Name, Title, Phone, Email

Colors
0054AA
0677BA
7BADD7
CADEEF
E8F1F8
0094D4
00A9DD
6FCCEA
C7EBF8
E9F6FB
00AB8E
00BBA5
67D7C9
C6EFE9
E9F9F6
59FF00
82FF00
B8FF75
E3FFCB
F4FFEA

```html
<!DOCTYPE html>
<html lang="en">
<head>
<meta charset="utf-8">
<title>Verodex business card</title>
<link href="https://fonts.googleapis.com/css2?family=Open+Sans:wght@400;600;700&display=swap" rel="stylesheet">
<style>
  :root {
    --bg: #e9eef2;
    --card: #fdfdf4;
    --navy: #13294f;
    --blue: #4a7fc2;
    --sky: #66c8d8;
    --name: #4a8fcb;
    --ink: #111111;
  }
  * { box-sizing: border-box; margin: 0; padding: 0; }
  html, body { width: 1200px; height: 780px; overflow: hidden; }
  body {
    background: var(--bg);
    font-family: "Open Sans", Arial, sans-serif;
    display: flex; align-items: center; justify-content: center; gap: 40px;
  }
  .card {
    position: relative;
    width: 540px; height: 309px;
    background: var(--card);
    border-radius: 22px;
    overflow: hidden;
    box-shadow: 0 6px 18px rgba(0,0,0,.18);
  }
  .card-bands { position: absolute; inset: 0; width: 100%; height: 100%; }
  .card-front .brand {
    position: absolute; left: 0; right: 0; top: 100px;
    display: flex; align-items: center; justify-content: center; gap: 18px;
  }
  .brand-dot {
    width: 34px; height: 34px; border-radius: 50%; background: var(--blue);
  }
  .card-front .brand-name {
    font-weight: 700; font-size: 58px; letter-spacing: 2px;
    color: var(--navy); text-transform: uppercase; line-height: 1;
  }
  .card-back .brand {
    position: absolute; left: 40px; top: 96px; width: 190px;
    display: flex; flex-direction: column; align-items: center; gap: 12px;
  }
  .card-back .brand-dot { width: 54px; height: 54px; }
  .card-back .brand-name {
    font-weight: 700; font-size: 38px; color: var(--blue); line-height: 1;
  }
  .divider {
    position: absolute; left: 262px; top: 62px; width: 1px; height: 130px;
    background: var(--navy);
  }
  .contact { position: absolute; left: 290px; top: 62px; }
  .person-name { font-weight: 700; font-size: 26px; color: var(--name); line-height: 1.1; }
  .person-title { font-weight: 600; font-size: 14px; color: var(--ink); margin-top: 2px; }
  .contact-list { list-style: none; margin-top: 18px; }
  .contact-list li {
    display: flex; align-items: center; gap: 8px;
    font-size: 13px; color: var(--ink); line-height: 1.5;
  }
  .contact-list svg { width: 12px; height: 12px; flex: none; }
  .address {
    position: absolute; left: 0; right: 0; top: 212px;
    text-align: center; font-size: 13px; color: var(--ink); padding-left: 80px;
  }
</style>
</head>
<body>
  <section class="card card-front">
    <svg class="card-bands" viewBox="0 0 540 309" preserveAspectRatio="none" aria-hidden="true">
      <defs>
        <linearGradient id="band-front" x1="0" y1="0" x2="1" y2="0">
          <stop offset="0" stop-color="#66c8d8"/>
          <stop offset="1" stop-color="#4a7fc2"/>
        </linearGradient>
      </defs>
      <path d="M0 309 L0 298 L365 262 L392 262 L350 309 Z" fill="url(#band-front)"/>
      <path d="M378 254 L540 220 L540 309 L362 309 L402 262 Z" fill="var(--navy)"/>
    </svg>
    <div class="brand">
      <span class="brand-dot"></span>
      <span class="brand-name">Verodex</span>
    </div>
  </section>

  <section class="card card-back">
    <svg class="card-bands" viewBox="0 0 540 309" preserveAspectRatio="none" aria-hidden="true">
      <defs>
        <linearGradient id="band-back" x1="0" y1="0" x2="1" y2="0">
          <stop offset="0" stop-color="#66c8d8"/>
          <stop offset="1" stop-color="#4a7fc2"/>
        </linearGradient>
      </defs>
      <path d="M0 309 L0 298 L365 262 L392 262 L350 309 Z" fill="url(#band-back)"/>
      <path d="M378 254 L540 220 L540 309 L362 309 L402 262 Z" fill="var(--navy)"/>
    </svg>
    <div class="brand">
      <span class="brand-dot"></span>
      <span class="brand-name">Verodex</span>
    </div>
    <div class="divider"></div>
    <div class="contact">
      <p class="person-name">Lena Marwick</p>
      <p class="person-title">Managing Director</p>
      <ul class="contact-list">
        <li><svg viewBox="0 0 12 12"><path d="M3 1 L5 3.5 L4 5 Q5 7 7 8 L8.5 7 L11 9 L9.5 11 Q4 10.5 1 3 Z" fill="#4a8fcb"/></svg>(512) 404-3187</li>
        <li><svg viewBox="0 0 12 12"><rect x="1" y="2.5" width="10" height="7" rx="1" fill="#4a8fcb"/><path d="M1.5 3 L6 6.5 L10.5 3" stroke="#fff" fill="none"/></svg>info@verodex.com</li>
        <li><svg viewBox="0 0 12 12"><circle cx="6" cy="6" r="5" fill="#4a8fcb"/><path d="M1 6 H11 M6 1 Q3 6 6 11 Q9 6 6 1" stroke="#fff" stroke-width=".8" fill="none"/></svg>www.verodex.com</li>
      </ul>
    </div>
    <p class="address">1840 Linden Ave. Suite 300 Austin, TX 78704</p>
  </section>
</body>
</html>
```